Maple Roster Business Card for recruitment company

We are looking for a Business Card Design that incorporates our personal details and our busines name and logo. We are a specialized search consultancy that recruit Property and Construction professionals.
We would like a business card that stands out and is appealing to the Construction and Property industry as well.

Target Market(s)

people in the construction and property industry

Contact Information for Business Card

Business Name and logo

Font styles to use
Serif

Colors
0094D4
00A9DD
6FCCEA
C7EBF8
E9F6FB

Requirements
Must have
• Business name and logo as well as contact details
Should not have
• No photos of us please

```html
<!DOCTYPE html>
<html lang="en">
<head>
<meta charset="utf-8">
<title>Maple Roster – Business Card</title>
<link rel="stylesheet" href="https://fonts.googleapis.com/css2?family=Questrial&family=Montserrat:wght@700&display=swap">
<style>
  :root {
    --backdrop: #e6eaed;
    --card-navy: #0a374b;
    --card-navy-deep: #062a3a;
    --ink-white: #ffffff;
    --blade-light: #ffffff;
    --blade-shade: #d4d8db;
    --shadow: rgba(0, 0, 0, 0.28);
  }
  * { margin: 0; padding: 0; box-sizing: border-box; }
  html, body { width: 1200px; height: 732px; overflow: hidden; }
  body {
    background: var(--backdrop);
    font-family: "Questrial", "Century Gothic", sans-serif;
    color: var(--ink-white);
    position: relative;
  }
  .card {
    position: absolute;
    top: 242px;
    width: 436px;
    height: 248px;
    background: linear-gradient(135deg, var(--card-navy) 0%, var(--card-navy) 50%, var(--card-navy-deep) 100%);
    box-shadow: 4px 6px 12px var(--shadow);
    overflow: hidden;
  }
  .card--front { left: 144px; }
  .card--back { left: 621px; }
  .card__blade {
    position: absolute;
    inset: 0;
    width: 100%;
    height: 100%;
  }
  .brand-name {
    position: absolute;
    left: 16px;
    top: 14px;
    font-family: "Questrial", "Century Gothic", sans-serif;
    font-size: 30px;
    line-height: 1;
    letter-spacing: 0.5px;
    color: var(--ink-white);
    text-transform: uppercase;
  }
  .brand-name--back {
    top: 164px;
    font-size: 22px;
  }
  .person {
    position: absolute;
    right: 18px;
    top: 147px;
    text-align: right;
  }
  .person__name {
    font-family: "Montserrat", "Century Gothic", sans-serif;
    font-weight: 700;
    font-size: 16px;
    line-height: 18px;
  }
  .person__role {
    font-size: 12.5px;
    line-height: 16px;
    letter-spacing: 0.3px;
  }
  .contact {
    position: absolute;
    right: 18px;
    top: 193px;
    list-style: none;
    text-align: right;
    font-size: 12.5px;
    line-height: 14.2px;
  }
  .contact__label {
    font-family: "Montserrat", "Century Gothic", sans-serif;
    font-weight: 700;
    font-size: 11px;
    margin-right: 8px;
  }
</style>
</head>
<body>
  <section class="card card--front" aria-label="Business card front">
    <svg class="card__blade" viewBox="0 0 436 248" aria-hidden="true">
      <defs>
        <linearGradient id="bladeFront" x1="0" y1="0" x2="0" y2="1">
          <stop offset="0" stop-color="var(--blade-light)"/>
          <stop offset="1" stop-color="var(--blade-shade)"/>
        </linearGradient>
      </defs>
      <polygon points="286,0 327,0 101,248" fill="url(#bladeFront)"/>
    </svg>
    <div class="brand-name">Maple Roster</div>
    <div class="person">
      <p class="person__name">Claire Hensley</p>
      <p class="person__role">Director&nbsp; | &nbsp;Senior Search Consultant</p>
    </div>
    <ul class="contact">
      <li><span class="contact__label">T:</span> +64 27 555 0142</li>
      <li><span class="contact__label">E:</span> claire@mapleroster.nz</li>
      <li><span class="contact__label">W:</span>www.mapleroster.nz</li>
    </ul>
  </section>

  <section class="card card--back" aria-label="Business card back">
    <svg class="card__blade" viewBox="0 0 436 248" aria-hidden="true">
      <defs>
        <linearGradient id="bladeBack" x1="0" y1="0" x2="0" y2="1">
          <stop offset="0" stop-color="var(--blade-light)"/>
          <stop offset="1" stop-color="var(--blade-shade)"/>
        </linearGradient>
      </defs>
      <polygon points="108,0 150,0 335,248" fill="url(#bladeBack)"/>
    </svg>
    <div class="brand-name brand-name--back">Maple Roster</div>
  </section>
</body>
</html>
```